Redesign of business card for Cedar Ridge Mechanical

We are looking for a new design for our business cards for Cedar Ridge Mechanical. We are a plumbing & HVAC construction company, operating on the West Coast of Canada and USA. Logo attached.
Industry/Entity Type
Construction - Plumbing & HVAC
Contact Information for Business Card
Name, address, phone numbers, email, website address
Look and feel
Each slider illustrates characteristics of the customer's brand and the style your logo design should communicate.

```html
<!DOCTYPE html>
<html lang="en">
<head>
<meta charset="utf-8">
<title>Cedar Ridge Mechanical – Business Card</title>
<link rel="stylesheet" href="https://fonts.googleapis.com/css2?family=Montserrat:wght@300;400;600&family=Oswald:wght@400&display=swap">
<style>
  :root {
    --page-bg: #e9e6e1;
    --card-bg: #262626;
    --ink: #ffffff;
    --ink-soft: #e6e6e6;
    --shadow: rgba(0, 0, 0, 0.28);
  }
  * { margin: 0; padding: 0; box-sizing: border-box; }
  html, body {
    width: 900px;
    height: 1200px;
    overflow: hidden;
    background: var(--page-bg);
  }
  .canvas {
    position: relative;
    width: 900px;
    height: 1200px;
  }
  .card {
    position: absolute;
    left: 80px;
    width: 742px;
    height: 442px;
    background: var(--card-bg);
    border-radius: 24px;
    box-shadow: 0 10px 24px var(--shadow);
    color: var(--ink);
    overflow: hidden;
  }
  .card--front { top: 130px; }
  .card--back { top: 637px; }

  .company-title {
    position: absolute;
    left: 35px;
    top: 48px;
    font-family: "Oswald", sans-serif;
    font-weight: 400;
    font-size: 34px;
    letter-spacing: 1.2px;
    text-transform: uppercase;
    line-height: 1;
  }
  .person {
    position: absolute;
    right: 56px;
    top: 38px;
    text-align: right;
    font-family: "Montserrat", sans-serif;
  }
  .person__name {
    font-weight: 600;
    font-size: 24px;
    line-height: 1.2;
  }
  .person__role {
    font-weight: 400;
    font-size: 15px;
    color: var(--ink-soft);
    margin-top: 2px;
  }
  .address {
    position: absolute;
    left: 35px;
    top: 243px;
    font-family: "Montserrat", sans-serif;
    font-weight: 300;
    font-size: 16px;
    line-height: 20px;
    font-style: normal;
  }
  .contact-list {
    position: absolute;
    left: 33px;
    top: 323px;
    list-style: none;
    font-family: "Montserrat", sans-serif;
    font-weight: 300;
    font-size: 15.5px;
  }
  .contact-list li {
    display: flex;
    align-items: center;
    height: 30.5px;
  }
  .contact-list svg {
    width: 16px;
    height: 16px;
    margin-right: 9px;
    fill: var(--ink);
    flex-shrink: 0;
  }

  .brand-mark {
    position: absolute;
    display: flex;
    align-items: center;
    font-family: "Oswald", sans-serif;
    font-weight: 400;
    text-transform: uppercase;
    color: var(--ink);
  }
  .brand-mark__square {
    background: var(--ink);
    flex-shrink: 0;
  }
  .brand-mark--front {
    right: 44px;
    bottom: 40px;
    font-size: 26px;
    letter-spacing: 1px;
    gap: 12px;
  }
  .brand-mark--front .brand-mark__square { width: 22px; height: 22px; }
  .brand-mark--back {
    left: 0;
    right: 0;
    top: 0;
    bottom: 0;
    justify-content: center;
    font-size: 40px;
    letter-spacing: 1.5px;
    gap: 18px;
  }
  .brand-mark--back .brand-mark__square { width: 34px; height: 34px; }
</style>
</head>
<body>
<main class="canvas">

  <section class="card card--front" aria-label="Business card front">
    <h1 class="company-title">Cedar Ridge Mechanical</h1>

    <div class="person">
      <p class="person__name">Daniel Brooks</p>
      <p class="person__role">Managing Director</p>
    </div>

    <address class="address">
      482 Birch Hollow Lane<br>
      Clinton, MS 39056
    </address>

    <ul class="contact-list">
      <li>
        <svg viewBox="0 0 24 24" aria-hidden="true"><path d="M6.6 10.8a15.1 15.1 0 0 0 6.6 6.6l2.2-2.2a1 1 0 0 1 1-.25 11.4 11.4 0 0 0 3.6.57 1 1 0 0 1 1 1V20a1 1 0 0 1-1 1A17 17 0 0 1 3 4a1 1 0 0 1 1-1h3.5a1 1 0 0 1 1 1c0 1.25.2 2.45.57 3.57a1 1 0 0 1-.25 1z"/></svg>
        888.555.0142
      </li>
      <li>
        <svg viewBox="0 0 24 24" aria-hidden="true"><path d="M2 5h20v2.2l-10 6-10-6z"/><path d="M2 9.5l10 6 10-6V19H2z"/></svg>
        info@cedarridgemechanical.com
      </li>
      <li>
        <svg viewBox="0 0 24 24" aria-hidden="true"><path d="M12 2a10 10 0 1 0 0 20 10 10 0 0 0 0-20zm0 2c.9 0 2.2 1.9 2.8 5H9.2C9.8 5.9 11.1 4 12 4zM4.3 14a8 8 0 0 1 0-4h2.9a17 17 0 0 0 0 4zm.8 2h2.4c.3 1.3.8 2.5 1.4 3.4A8 8 0 0 1 5.1 16zm2.4-8H5.1a8 8 0 0 1 3.8-3.4C8.3 5.5 7.8 6.7 7.5 8zM12 20c-.9 0-2.2-1.9-2.8-4h5.6c-.6 2.1-1.9 4-2.8 4zm3.1-6H8.9a15 15 0 0 1 0-4h6.2a15 15 0 0 1 0 4zm0 5.4c.6-.9 1.1-2.1 1.4-3.4h2.4a8 8 0 0 1-3.8 3.4zm1.7-5.4a17 17 0 0 0 0-4h2.9a8 8 0 0 1 0 4zm-.3-6c-.3-1.3-.8-2.5-1.4-3.4A8 8 0 0 1 18.9 8z"/></svg>
        www.cedarridgemechanical.com
      </li>
    </ul>

    <div class="brand-mark brand-mark--front">
      <span class="brand-mark__square" aria-hidden="true"></span>
      <span class="brand-mark__name">Cedar Ridge Mechanical</span>
    </div>
  </section>

  <section class="card card--back" aria-label="Business card back">
    <div class="brand-mark brand-mark--back">
      <span class="brand-mark__square" aria-hidden="true"></span>
      <span class="brand-mark__name">Cedar Ridge Mechanical</span>
    </div>
  </section>

</main>
</body>
</html>
```